Modern Business Card

Modern professional business card with more than just logo and demographic info. Something memorable.

We are a trendy/modern chiropractic group with an emphasis on neurology, hence the minimalist-type brain logo. We want to convey that modern and technical aspect with professionalism and the elite nature of our practice environment.

```html
<!DOCTYPE html>
<html lang="en">
<head>
<meta charset="utf-8">
<title>Keystone Spine Care – Business Card</title>
<link rel="stylesheet" href="https://fonts.googleapis.com/css2?family=Cinzel:wght@500&family=Montserrat:wght@400;500&display=swap">
<style>
  :root {
    --bg: #3a332f;
    --card: #141517;
    --card-edge: #2e5fa8;
    --blue: #3b74c9;
    --white: #f2f2f2;
    --grey: #b9bcc2;
  }
  * { box-sizing: border-box; margin: 0; padding: 0; }
  html, body { width: 1200px; height: 716px; overflow: hidden; }
  body {
    background: var(--bg);
    position: relative;
    font-family: "Montserrat", sans-serif;
  }
  .card {
    position: absolute;
    width: 520px;
    height: 297px;
    background: var(--card);
    border-radius: 6px;
    box-shadow: 0 14px 30px rgba(0,0,0,.45);
  }
  .card-front {
    left: 60px; top: 140px;
    border-bottom: 6px solid var(--card-edge);
    border-right: 4px solid var(--card-edge);
    display: flex; align-items: center; justify-content: center;
  }
  .card-back { left: 620px; top: 300px; }

  .brand {
    display: flex; align-items: center; gap: 14px;
    font-family: "Cinzel", serif;
    font-weight: 500;
    color: var(--white);
    line-height: 1.05;
  }
  .brand-mark {
    width: 14px; height: 14px;
    background: var(--blue);
    flex: none;
  }
  .card-front .brand { font-size: 34px; letter-spacing: 1px; }
  .card-back .brand { font-size: 22px; letter-spacing: .5px; position: absolute; left: 36px; top: 120px; }

  .divider {
    position: absolute; left: 282px; top: 58px;
    width: 2px; height: 190px;
    background: linear-gradient(var(--blue) 0 22%, transparent 22% 30%, var(--white) 30%);
  }
  .contact {
    position: absolute; left: 306px; top: 62px;
    color: var(--white);
    font-size: 12.5px;
    line-height: 1.5;
  }
  .contact-name {
    font-family: "Cinzel", serif;
    font-weight: 500;
    color: var(--blue);
    font-size: 17px;
    letter-spacing: .5px;
  }
  .contact-role { margin-bottom: 6px; }
  .contact-address { margin-bottom: 6px; }
  .contact-line { display: flex; align-items: center; gap: 8px; }
  .contact-line svg { width: 11px; height: 11px; flex: none; }
  .accent { color: var(--blue); }
</style>
</head>
<body>
  <section class="card card-front" aria-label="Card front">
    <div class="brand"><span class="brand-mark"></span><span>Keystone<br>Spine Care</span></div>
  </section>

  <section class="card card-back" aria-label="Card back">
    <div class="brand"><span class="brand-mark"></span><span>Keystone<br>Spine Care</span></div>
    <div class="divider"></div>
    <div class="contact">
      <p class="contact-name">Martin Ellery</p>
      <p class="contact-role">Director</p>
      <p class="contact-address">118 Cedar Mill Road<br>Salem, OR 97301</p>
      <p class="contact-line">
        <svg viewBox="0 0 12 12" aria-hidden="true"><path d="M3 1l2 2.5-1.2 1.3a7 7 0 0 0 3.4 3.4L8.5 7 11 9l-1 2C5 11 1 7 1 2z" fill="var(--blue)"/></svg>
        (555) 018-2746
      </p>
      <p class="contact-line">
        <svg viewBox="0 0 12 12" aria-hidden="true"><rect x="1" y="2.5" width="10" height="7" fill="none" stroke="var(--blue)" stroke-width="1.2"/><path d="M1 2.5l5 4 5-4" fill="none" stroke="var(--blue)" stroke-width="1.2"/></svg>
        info@keystonespine.com
      </p>
      <p class="contact-line">
        <svg viewBox="0 0 12 12" aria-hidden="true"><circle cx="6" cy="6" r="5" fill="none" stroke="var(--blue)" stroke-width="1.2"/><path d="M1 6h10M6 1c-2.5 3-2.5 7 0 10M6 1c2.5 3 2.5 7 0 10" fill="none" stroke="var(--blue)" stroke-width="1"/></svg>
        <span>www.<span class="accent">keystonespine</span>.com</span>
      </p>
    </div>
  </section>
</body>
</html>
```